Marwick Partners Exit Plan business consultant web site

This website is for a consulting business that helps other businesses with exit plans. Essentially, assists them with the sale of their business. This website should be very professional, almost with a wall street look. I would like a very attractive image on the homepage. Perhaps something that denotes success. Perhaps a picture of palm trees and a beach? I will leave it to you for interpretation.

Across the screen I would like the words "Does your business have an exit plan?"

Below that it should read the following:
Let us help you with a completely impartial, no obligation assessment (button with link to the contact page)

Also, please use logo in a prominent place on the website so it's easily seen.

Target Market(s)

Males 40+

Coding

Coded - Design and coding required

Number of Pages Required

5+ page

Colors

Designer to choose colors to be used in the design.

Requirements
Must have
• The tabs for the homepage on the top should be:
• 1. About us
• 2. Services
• 3. Industries
• 4. Our success
• 5. Contact
Nice to have
• Clean, professional image.
• Please put FB, Twitter, Linked In - logos at bottom.
• Here are two examples of a website to give you an idea:
• https://notes.quelvarocapital.example/library/why-every-business-owner-should-have-an-exit-plan
Should not have
• nothing whimsical or cartoon like

```html
<!DOCTYPE html>
<html lang="en">
<head>
<meta charset="utf-8">
<title>Marwick Partners — Exit Planning Consultants</title>
<link rel="stylesheet" href="https://fonts.googleapis.com/css2?family=Martel:wght@300;400;600&family=Roboto:wght@400&display=swap">
<style>
:root{
  --blue:#2286c9;
  --navy:#1f3a5c;
  --text:#555;
  --white:#fff;
  --light:#f5f5f5;
  --footer:#1f1f1f;
  --border:#d6d6d6;
}
*{margin:0;padding:0;box-sizing:border-box}
html,body{width:1200px;height:3229px;overflow:hidden}
body{position:relative;font-family:"Martel",Georgia,serif;color:var(--text);background:var(--white);line-height:1.3}
.abs{position:absolute}
.center{left:0;width:1200px;text-align:center}

/* hero */
.hero{position:absolute;left:0;top:0;width:1200px;height:667px;overflow:hidden;
  background:
    radial-gradient(ellipse 180px 150px at 380px 260px,rgba(214,150,70,.55),rgba(214,150,70,0)),
    linear-gradient(180deg,#4a4d52 0%,#34322f 28%,#3d2d1c 58%,#4a3418 72%,#1d1813 100%)}
.hero-band{position:absolute;left:0;width:1200px;background:rgba(0,0,0,.25)}
.brand-mark{position:absolute;left:567px;top:38px;width:66px;height:79px;border:3px solid var(--white)}
.brand-name{top:124px;font-size:26px;line-height:28px;font-weight:300;letter-spacing:1px;color:var(--white);text-transform:uppercase}
.nav-item{position:absolute;top:180px;font-size:13px;line-height:16px;color:var(--white);text-transform:uppercase;transform:translateX(-50%)}
.nav-pill{position:absolute;left:213px;top:169px;width:84px;height:38px;border:1px solid var(--white);border-radius:19px}
.hero-title{top:400px;font-size:42px;line-height:46px;font-weight:400;color:var(--white);text-transform:uppercase}
.hero-sub{top:460px;font-size:15px;line-height:18px;color:var(--white)}
.btn{position:absolute;background:var(--blue);color:var(--white);border-radius:30px;text-align:center}
.hero-btn{left:494px;top:505px;width:212px;height:59px;line-height:64px;font-size:17px;text-transform:uppercase}
.dot{position:absolute;top:638px;width:9px;height:9px;border-radius:50%;background:var(--white)}
.dot.active{background:var(--blue)}

/* services */
.section-title{font-size:38px;line-height:44px;font-weight:400;color:var(--blue)}
.section-sub{font-size:14px;line-height:18px;color:#444}
.card{position:absolute;top:840px;width:225px;height:286px;background:var(--white);
  box-shadow:0 0 6px rgba(0,0,0,.18);text-align:center}
.card svg{position:absolute;left:55px;top:26px}
.card h3{position:absolute;left:0;width:225px;top:155px;font-size:18px;line-height:24px;font-weight:400;color:var(--navy)}
.card p{position:absolute;left:12px;width:201px;top:190px;font-size:11.5px;line-height:24px;color:#666}

/* about */
.about{position:absolute;left:0;top:1194px;width:1200px;height:419px;
  background:
    radial-gradient(ellipse 260px 200px at 200px 180px,#cfd1d5,rgba(207,209,213,0)),
    radial-gradient(ellipse 260px 200px at 1000px 200px,#d3d5d8,rgba(211,213,216,0)),
    linear-gradient(90deg,#dcdde0,#eeeeef 45%,#e8e9ea 60%,#dadbde)}
.about-title{top:1270px;font-size:70px;line-height:74px;font-weight:400;color:var(--blue)}
.about-text{left:260px;width:680px;top:1368px;font-size:14.5px;line-height:31px;color:#444;text-align:center}
.about-btn{left:474px;top:1487px;width:252px;height:57px;line-height:62px;font-size:15px}

/* feature rows */
.photo{position:absolute;width:600px;height:408px}
.feature h2{position:absolute;font-size:35px;line-height:40px;font-weight:400;color:var(--blue)}
.rule{position:absolute;height:4px;width:61px;background:var(--blue)}
.feature p{position:absolute;width:432px;font-size:11.4px;line-height:25.6px;color:#555;text-align:justify;letter-spacing:-.1px}
.learn{position:absolute;font-size:15px;line-height:18px;color:var(--blue);display:flex;align-items:center;gap:7px}

/* contact */
.contact{position:absolute;left:0;top:2429px;width:1200px;height:489px;background:var(--light)}
.field{position:absolute;background:var(--white);border:1px solid var(--border);
  font-family:"Roboto",Arial,sans-serif;font-size:14px;line-height:18px;color:#555;padding:13px 14px}
.submit{left:508px;top:2815px;width:185px;height:54px;line-height:60px;font-size:18px;text-transform:uppercase}

/* footer */
.footer{position:absolute;left:0;top:2918px;width:1200px;height:311px;background:var(--footer)}
.foot-nav{position:absolute;top:3078px;font-size:12.5px;line-height:16px;color:var(--white);text-transform:uppercase;transform:translateX(-50%)}
.copyright{top:3184px;font-size:13px;line-height:16px;color:var(--white)}
</style>
</head>
<body>

<header class="hero" role="img" aria-label="Business people silhouetted against a city skyline at sunset">
  <div class="hero-band" style="top:290px;height:6px"></div>
  <div class="hero-band" style="top:250px;height:3px"></div>
</header>
<div class="brand-mark"></div>
<div class="abs center brand-name">Marwick Partners</div>

<nav>
  <div class="nav-pill"></div>
  <span class="nav-item" style="left:255px">Home</span>
  <span class="nav-item" style="left:375px">About Us</span>
  <span class="nav-item" style="left:504px">Services</span>
  <span class="nav-item" style="left:642px">Industries</span>
  <span class="nav-item" style="left:791px">Our Success</span>
  <span class="nav-item" style="left:933px">Contact</span>
</nav>

<h1 class="abs center hero-title">Does your business have an exit plan</h1>
<p class="abs center hero-sub">Let us help you with a completely impartial, no obligation assessment</p>
<div class="btn hero-btn">Contact Us</div>
<span class="dot" style="left:577px"></span>
<span class="dot active" style="left:596px"></span>
<span class="dot" style="left:614px"></span>

<!-- services -->
<h2 class="abs center section-title" style="top:720px">Our Services</h2>
<p class="abs center section-sub" style="top:783px">Sed ut perspiciatis unde omnis iste natus error sit voluptatem accusantium doloremque</p>

<div class="card" style="left:112px">
  <svg width="114" height="114" viewBox="0 0 114 114"><circle cx="57" cy="57" r="57" fill="#2286c9"/>
    <circle cx="50" cy="52" r="10" fill="#fff"/><path d="M30 80c2-12 10-17 20-17s18 5 20 17z" fill="#fff"/>
    <circle cx="72" cy="40" r="12" fill="none" stroke="#fff" stroke-width="3"/>
    <text x="72" y="46" fill="#fff" font-size="16" font-family="Arial,sans-serif" text-anchor="middle">$</text></svg>
  <h3>Accountant</h3>
  <p>Sed ut perspiciatis unde omnis iste natus error sit voluptatem accusantium doloremque</p>
</div>
<div class="card" style="left:362px">
  <svg width="114" height="114" viewBox="0 0 114 114"><circle cx="57" cy="57" r="57" fill="#2286c9"/>
    <circle cx="47" cy="30" r="7" fill="#fff"/><path d="M38 40h18v16h-5v26h-8V56h-5z" fill="#fff"/>
    <path d="M30 50l10-6" stroke="#fff" stroke-width="5" stroke-linecap="round"/>
    <text x="71" y="80" fill="#fff" font-size="34" font-weight="bold" font-family="Arial,sans-serif" text-anchor="middle">$</text></svg>
  <h3>Investment banker</h3>
  <p>Sed ut perspiciatis unde omnis iste natus error sit voluptatem accusantium doloremque</p>
</div>
<div class="card" style="left:612px">
  <svg width="114" height="114" viewBox="0 0 114 114"><circle cx="57" cy="57" r="57" fill="#2286c9"/>
    <rect x="32" y="28" width="34" height="48" fill="none" stroke="#fff" stroke-width="3"/>
    <path d="M38 40h20M38 48h20M38 56h14" stroke="#fff" stroke-width="3"/>
    <rect x="60" y="54" width="26" height="22" fill="#fff"/><circle cx="74" cy="40" r="6" fill="none" stroke="#fff" stroke-width="3"/></svg>
  <h3>Corporate attorney</h3>
  <p>Sed ut perspiciatis unde omnis iste natus error sit voluptatem accusantium doloremque</p>
</div>
<div class="card" style="left:861px">
  <svg width="114" height="114" viewBox="0 0 114 114"><circle cx="57" cy="57" r="57" fill="#2286c9"/>
    <circle cx="58" cy="40" r="13" fill="none" stroke="#fff" stroke-width="7" stroke-dasharray="5 3"/>
    <circle cx="58" cy="40" r="5" fill="#fff"/>
    <path d="M28 72c8-8 16-10 26-6h14c5 0 5 6 0 6H54M66 70l14-8c5-3 9 3 4 6L64 82H40" fill="none" stroke="#fff" stroke-width="5" stroke-linecap="round" stroke-linejoin="round"/></svg>
  <h3>Wealth planning</h3>
  <p>Sed ut perspiciatis unde omnis iste natus error sit voluptatem accusantium doloremque</p>
</div>

<!-- about -->
<section class="about" role="img" aria-label="Faded photo of colleagues working together at a desk"></section>
<h2 class="abs center about-title">ABOUT US</h2>
<p class="abs about-text">Sed ut perspiciatis unde omnis iste natus error sit voluptatem accusantium doloremque lau dantium, totam rem aperiam, eaque ipsa quae ab illo inventore veritatis et quasi architecto beatae vitae dicta sunt explicabo nemo enim ipsam voluptatem</p>
<div class="btn about-btn">Click Here For More Info</div>

<!-- our success -->
<section class="feature">
  <div class="photo" style="left:0;top:1613px;background:
    radial-gradient(ellipse 160px 90px at 300px 220px,rgba(226,120,60,.55),rgba(226,120,60,0)),
    linear-gradient(180deg,#a88f88 0%,#c4aaa0 30%,#8f8790 60%,#6a6670 100%)" role="img" aria-label="Team meeting around a conference table in a glass-walled office"></div>
  <h2 style="left:645px;top:1680px">Our Success</h2>
  <div class="rule" style="left:645px;top:1731px"></div>
  <p style="left:645px;top:1760px">Lorem ipsum dolor sit amet, consectetur adipiscing elit, sed do eiusmod tempor incididunt ut labore et dolore magna aliqua. Ut enim ad minim veniam, quis nostrud exercitation ullamco laboris nisi ut aliquip ex ea commodo consequat. Duis aute irure dolor in reprehenderit in voluptate velit esse cillum dolore eu fugiat nulla pariatur. Excepteur sint occaecat cupidatat non proident, sunt in culpa qui officia deserunt</p>
  <div class="learn" style="left:645px;top:1938px">Learn More
    <svg width="15" height="15" viewBox="0 0 16 16"><circle cx="8" cy="8" r="8" fill="#2286c9"/><path d="M6 4l4 4-4 4" fill="none" stroke="#fff" stroke-width="2"/></svg></div>
</section>

<!-- our industries -->
<section class="feature">
  <h2 style="left:132px;top:2088px">Our Industries</h2>
  <div class="rule" style="left:132px;top:2139px"></div>
  <p style="left:132px;top:2168px">Lorem ipsum dolor sit amet, consectetur adipiscing elit, sed do eiusmod tempor incididunt ut labore et dolore magna aliqua. Ut enim ad minim veniam, quis nostrud exercitation ullamco laboris nisi ut aliquip ex ea commodo consequat. Duis aute irure dolor in reprehenderit in voluptate velit esse cillum dolore eu fugiat nulla pariatur. Excepteur sint occaecat cupidatat non proident, sunt in culpa qui officia deserunt</p>
  <div class="learn" style="left:132px;top:2346px">Learn More
    <svg width="15" height="15" viewBox="0 0 16 16"><circle cx="8" cy="8" r="8" fill="#2286c9"/><path d="M6 4l4 4-4 4" fill="none" stroke="#fff" stroke-width="2"/></svg></div>
  <div class="photo" style="left:600px;top:2021px;background:
    radial-gradient(ellipse 70px 120px at 290px 200px,rgba(200,210,60,.55),rgba(200,210,60,0)),
    linear-gradient(180deg,#3d5e8a 0%,#4f76a3 40%,#2e4668 75%,#1f2c46 100%)" role="img" aria-label="Engineer in a hard hat and safety vest walking through a heavy industry plant"></div>
</section>

<!-- contact -->
<section class="contact"></section>
<h2 class="abs center section-title" style="top:2468px">Contact Us</h2>
<div class="rule" style="left:572px;top:2527px;width:55px;height:3px"></div>
<p class="abs center section-sub" style="top:2553px">Sed ut perspiciatis unde omnis iste natus error sit voluptatem accusantium doloremque</p>
<div class="field" style="left:272px;top:2612px;width:320px;height:45px">First Name*</div>
<div class="field" style="left:608px;top:2612px;width:320px;height:45px">Last Name*</div>
<div class="field" style="left:272px;top:2667px;width:320px;height:45px">Phone*</div>
<div class="field" style="left:608px;top:2667px;width:320px;height:45px">Email*</div>
<div class="field" style="left:272px;top:2722px;width:654px;height:72px">Company*</div>
<div class="btn submit">Submit</div>

<!-- footer -->
<footer class="footer"></footer>
<div class="brand-mark" style="top:2935px;height:81px"></div>
<div class="abs center brand-name" style="top:3022px">Marwick Partners</div>
<span class="foot-nav" style="left:312px">Home</span>
<span class="foot-nav" style="left:410px">About Us</span>
<span class="foot-nav" style="left:518px">Services</span>
<span class="foot-nav" style="left:632px">Industries</span>
<span class="foot-nav" style="left:759px">Our Success</span>
<span class="foot-nav" style="left:877px">Contact</span>
<svg class="abs" style="left:530px;top:3120px" width="140" height="42" viewBox="0 0 140 42" role="img" aria-label="Social profile links">
  <g fill="none" stroke="#fff" stroke-width="2">
    <circle cx="27" cy="21" r="18"/>
    <circle cx="69" cy="21" r="18"/>
    <circle cx="113" cy="21" r="18"/>
  </g>
</svg>
<p class="abs center copyright">© 2020 On Marwick Partners | All Rights Reserved</p>

</body>
</html>
```